Business cards and stationary design

We just completed the design of our new logo and we need to print new business cards and letterhead for our nonprofit. We are looking for a fresh new design that shows off our new logo. On letterhead, we must have a column on the right or left to include our Board of Directors (up to 45 names) (see attachment)

Industry/Entity Type

Non-Profit

Contact Information for Business Card

Standard business card with name, title, Company name, mailing address phone numbers, email address and website. Tagline on back "Bringing the homeless home"

Font styles to use
Sans Serif

Requirements
Must have
• include pertinent information above
• new logo
• fonts compatible with logo
• should use logo colors only
Nice to have
• tag lines

```html
<!DOCTYPE html>
<html lang="en">
<head>
<meta charset="utf-8">
<title>Quillmoor House – Business Card</title>
<link rel="stylesheet" href="https://fonts.googleapis.com/css2?family=Roboto:wght@400;500;700&display=swap">
<style>
  :root {
    --backdrop: #2a2a2a;
    --brand-red: #d72027;
    --brand-teal: #0a87a8;
    --paper: #f1f1f1;
    --ink: #4a4a4a;
    --ink-strong: #3c3c3c;
    --rule: #c9c9c9;
    --white: #ffffff;
  }
  * { margin: 0; padding: 0; box-sizing: border-box; }
  html, body {
    width: 1200px;
    height: 960px;
    overflow: hidden;
    background: var(--backdrop);
    font-family: "Roboto", Arial, sans-serif;
  }
  .canvas { position: relative; width: 1200px; height: 960px; }

  /* Card back */
  .card-back {
    position: absolute;
    left: 322px; top: 100px;
    width: 600px; height: 347px;
    background: var(--brand-red);
  }
  .card-back .org-mark {
    position: absolute;
    left: 0; right: 0; top: 150px;
    display: flex; align-items: center; justify-content: center; gap: 14px;
    color: var(--white);
    font-weight: 700;
    font-size: 34px;
    letter-spacing: 2px;
    text-transform: uppercase;
    white-space: nowrap;
  }
  .card-back .org-mark .mark-square {
    width: 22px; height: 22px; background: var(--white); flex: none;
  }
  .card-back .website {
    position: absolute;
    left: 0; right: 0; top: 299px;
    text-align: center;
    color: var(--white);
    font-size: 14px;
    letter-spacing: 4.4px;
  }

  /* Card front */
  .card-front {
    position: absolute;
    left: 320px; top: 493px;
    width: 600px; height: 342px;
    background: var(--paper);
  }
  .card-front .org-mark {
    position: absolute;
    left: 45px; width: 275px; top: 170px;
    display: flex; align-items: center; justify-content: center; gap: 10px;
    color: var(--brand-teal);
    font-weight: 500;
    font-size: 18px;
    letter-spacing: 1.5px;
    text-transform: uppercase;
    white-space: nowrap;
  }
  .card-front .org-mark .mark-circle {
    width: 14px; height: 14px; border-radius: 50%; background: var(--brand-teal); flex: none;
  }
  .card-front .divider {
    position: absolute;
    left: 328px; top: 82px;
    width: 1px; height: 160px;
    background: var(--rule);
  }
  .contact { position: absolute; left: 351px; top: 80px; color: var(--ink); }
  .contact .person-name {
    color: var(--brand-teal);
    font-weight: 700;
    font-size: 23px;
    line-height: 26px;
    text-transform: uppercase;
  }
  .contact .person-title {
    color: var(--brand-red);
    font-weight: 500;
    font-size: 15px;
    line-height: 18px;
    text-transform: uppercase;
  }
  .contact .address { margin-top: 11px; font-size: 14.5px; line-height: 18px; }
  .contact .address .org-name { font-weight: 700; color: var(--ink-strong); }
  .contact .lines { margin-top: 11px; font-size: 14.5px; line-height: 19px; }
  .contact .line { display: flex; align-items: center; gap: 8px; }
  .contact .line svg { width: 13px; height: 13px; fill: var(--brand-teal); }

  .card-front .rule-red {
    position: absolute; left: 0; right: 0; height: 2px; background: var(--brand-red);
  }
  .card-front .rule-top { top: 286px; }
  .card-front .rule-bottom { top: 322px; }
  .card-front .band {
    position: absolute; left: 0; right: 0; top: 291px; height: 28px;
    background: var(--brand-teal);
    color: var(--white);
    text-align: center;
    font-size: 15px;
    line-height: 28px;
    letter-spacing: 4.4px;
  }
</style>
</head>
<body>
<main class="canvas">
  <section class="card-back">
    <div class="org-mark"><span class="mark-square"></span>Quillmoor House</div>
    <p class="website">www.quillmoorhouse.org</p>
  </section>

  <section class="card-front">
    <div class="org-mark"><span class="mark-circle"></span>Quillmoor House</div>
    <div class="divider"></div>
    <div class="contact">
      <p class="person-name">Jordan Avery</p>
      <p class="person-title">CEO/Founder</p>
      <p class="address">
        <span class="org-name">Quillmoor House</span><br>
        214 Birchwood Avenue<br>
        Juneau, Alaska 99801
      </p>
      <div class="lines">
        <p class="line">
          <svg viewBox="0 0 24 24" aria-hidden="true"><path d="M6.6 10.8a15.1 15.1 0 0 0 6.6 6.6l2.2-2.2a1 1 0 0 1 1-.25 11.4 11.4 0 0 0 3.6.57 1 1 0 0 1 1 1V20a1 1 0 0 1-1 1A17 17 0 0 1 3 4a1 1 0 0 1 1-1h3.5a1 1 0 0 1 1 1c0 1.250.2 2.45.57 3.6a1 1 0 0 1-.25 1z"/></svg>
          555 014 2290
        </p>
        <p class="line">
          <svg viewBox="0 0 24 24" aria-hidden="true"><path d="M2 5h20v14H2z M4 7v.5l8 5 8-5V7z" fill-rule="evenodd"/></svg>
          jordan@quillmoorhouse.org
        </p>
      </div>
    </div>
    <div class="rule-red rule-top"></div>
    <div class="band">www.quillmoorhouse.org</div>
    <div class="rule-red rule-bottom"></div>
  </section>
</main>
</body>
</html>
```